Business Card for a mobile physiotherapy company

I need a layout for a business card for a mobile physiotherapy company.
Slogan is "Mobile Physiotherapy - Your Road To Recovery"
Phone number is 867-555-0142
Email VardenTherapy@postnest.ca (subject to change with website)
Website www.VardenTherapy.ca
My name and credentials: Luke Varden Luke Varden, BSc(kin), MPT, CAFCI, IMS
Information maybe included: Direct Billing, Services including Physiotherapy, IMS, acupuncture
Maybe include facebook and instagram logos
One side with the logo clean and sharp
Other side with details, try not to look too busy, keep everything concise

```html
<!DOCTYPE html>
<html lang="en">
<head>
<meta charset="utf-8">
<title>Varden Therapy – Business Card</title>
<link rel="stylesheet" href="https://fonts.googleapis.com/css2?family=Lato:wght@400;700&display=swap">
<style>
  :root {
    --bg: #9a9a9a;
    --green: #14594c;
    --green-dark: #0f4c40;
    --green-light: #1f6a5c;
    --navy: #2f4f7f;
    --white: #ffffff;
  }
  * { margin: 0; padding: 0; box-sizing: border-box; }
  html, body {
    width: 1200px; height: 930px; overflow: hidden;
    background: var(--bg);
    font-family: "Lato", sans-serif;
  }
  .card {
    position: absolute; left: 250px;
    width: 700px; height: 400px;
    border-radius: 26px; overflow: hidden;
    box-shadow: 0 6px 18px rgba(0,0,0,0.3);
  }
  .card--front { top: 40px; background: linear-gradient(135deg, var(--green-light), var(--green) 55%, var(--green-dark)); }
  .card--back { top: 490px; background: linear-gradient(135deg, var(--green-dark), var(--green) 60%, var(--green-light)); }

  .brand {
    display: flex; align-items: center; gap: 12px;
    font-weight: 700; letter-spacing: 0.14em; text-transform: uppercase;
    line-height: 1;
  }
  .brand__mark { width: 14px; height: 14px; flex: none; }
  .card--front .brand {
    position: absolute; left: 0; right: 0; top: 150px;
    justify-content: center; color: var(--white); font-size: 44px;
  }
  .card--front .brand__mark { background: var(--white); }
  .slogan {
    position: absolute; left: 0; right: 0; top: 320px;
    text-align: center; color: var(--white); font-size: 17px; letter-spacing: 0.02em;
  }

  .back-art { position: absolute; inset: 0; width: 700px; height: 400px; }
  .card--back .brand {
    position: absolute; right: 45px; top: 80px;
    color: var(--green); font-size: 32px;
  }
  .card--back .brand__mark { background: var(--navy); width: 12px; height: 12px; }

  .details {
    position: absolute; left: 40px; top: 205px; color: var(--white);
  }
  .details__name { font-size: 23px; font-weight: 400; line-height: 1.15; margin-bottom: 8px; }
  .details__services { font-size: 14px; line-height: 1.35; margin-bottom: 10px; }
  .contact { list-style: none; font-size: 15px; }
  .contact li { display: flex; align-items: center; gap: 10px; line-height: 1.55; }
  .contact svg { width: 14px; height: 14px; flex: none; }
</style>
</head>
<body>

<section class="card card--front" aria-label="Card front">
  <div class="brand"><span class="brand__mark"></span>Varden Therapy</div>
  <p class="slogan">Mobile Physiotherapy - Your Road To Recovery</p>
</section>

<section class="card card--back" aria-label="Card back">
  <svg class="back-art" viewBox="0 0 700 400" aria-hidden="true">
    <path d="M150,0 C200,230 440,300 700,255 L700,0 Z" fill="#2f4f7f"/>
    <path d="M165,0 C214,215 446,283 700,243 L700,0 Z" fill="#ffffff"/>
  </svg>

  <div class="brand"><span class="brand__mark"></span>Varden Therapy</div>

  <div class="details">
    <h1 class="details__name">Luke Varden, BSc(kin),<br>MPT, CAFCI, IMS</h1>
    <p class="details__services">Direct Billing, Services including<br>Physiotherapy, IMS, acupuncture</p>
    <ul class="contact">
      <li>
        <svg viewBox="0 0 24 24" aria-hidden="true"><path fill="#fff" d="M6.6 10.8a15 15 0 0 0 6.6 6.6l2.2-2.2a1 1 0 0 1 1-.25 11.4 11.4 0 0 0 3.6.57 1 1 0 0 1 1 1V20a1 1 0 0 1-1 1A17 17 0 0 1 3 4a1 1 0 0 1 1-1h3.5a1 1 0 0 1 1 1c0 1.25.2 2.45.57 3.57a1 1 0 0 1-.25 1z"/></svg>
        867-555-0142
      </li>
      <li>
        <svg viewBox="0 0 24 24" aria-hidden="true"><rect x="3" y="5" width="18" height="14" rx="2" fill="none" stroke="#fff" stroke-width="2"/><path d="M3 6l9 7 9-7" fill="none" stroke="#fff" stroke-width="2"/></svg>
        VardenTherapy@postnest.ca
      </li>
      <li>
        <svg viewBox="0 0 24 24" aria-hidden="true"><circle cx="12" cy="12" r="9" fill="none" stroke="#fff" stroke-width="2"/><path d="M3 12h18M12 3c3 3 3 15 0 18M12 3c-3 3-3 15 0 18" fill="none" stroke="#fff" stroke-width="1.6"/></svg>
        www.VardenTherapy.ca
      </li>
    </ul>
  </div>
</section>

</body>
</html>
```